Want to fly? Flight school needs a roll up

Hello designers

We are a small aviation club with around 100 members. We love flying and therefore offer free flight lessons for young people at our glider flight school.
The young people only have to pay a flat rate of €300 for the aircraft until their first solo flight.
To advertise the flight school we now need a roll up banner measuring 85cm x 200cm. You can find the data sheet for the banner in the appendix.
Content of the roll up banner:
Advertising for our flight school so that we can attract new members
The banner should be designed in our club colors blue/white
The banner is aimed at all people who want to get a glider license
A great offer for young people up to the age of 25 should be placed on the banner with a reference to the text “Offer only applies to people up to the age of 25. Included in the flat rate of €300 is training on the glider up to the first "solo flight"
The banner is intended to advertise training with a glider. Therefore the wish would be for a glider to be depicted

Here is a link to our current homepage

https://www.lgk-tarnholm.de/

https://www.vidoplex.example/watch?v=Qk7pL2xNz9c

Target Market(s)

Young people from 14 years to 30 years

Colors
0054AA
0677BA
7BADD7
CADEEF
E8F1F8

Requirements
Nice to have
• Glider / club logo
Should not have
• Too much text

```html
<!DOCTYPE html>
<html lang="en">
<head>
<meta charset="utf-8">
<title>Free Flight Lessons – Roll-up</title>
<link rel="stylesheet" href="https://fonts.googleapis.com/css2?family=Poppins:wght@800&family=Bebas+Neue&family=Roboto+Condensed:wght@700&display=swap">
<style>
  :root {
    --navy: #1a2055;
    --ring: #1f2fa8;
    --white: #ffffff;
    --paper: #f2f2f2;
    --red: #e8141c;
    --stage: #ffffff;
  }
  * { margin: 0; padding: 0; box-sizing: border-box; }
  html, body { width: 1200px; height: 4000px; overflow: hidden; background: var(--stage); }
  .rollup {
    position: absolute; left: 50px; top: 706px;
    width: 1100px; height: 2588px;
    background: var(--white);
    box-shadow: 0 4px 18px rgba(0,0,0,.35);
    overflow: hidden;
  }
  .rollup__backdrop { position: absolute; inset: 0; }
  .club-mark {
    position: absolute; left: 383px; top: 45px; width: 316px; height: 316px;
    border-radius: 50%; background: var(--white);
    display: flex; flex-direction: column; align-items: center; justify-content: center; gap: 14px;
  }
  .club-mark__dot { width: 40px; height: 40px; border-radius: 50%; background: var(--ring); }
  .club-mark__name {
    font-family: "Roboto Condensed", sans-serif; font-weight: 700; font-size: 30px;
    color: var(--ring); text-align: center; line-height: 1.15;
  }
  .headline {
    position: absolute; left: 0; width: 100%; text-align: center;
    font-family: "Poppins", sans-serif; font-weight: 800; color: var(--white); line-height: 1;
  }
  .headline--free { top: 418px; font-size: 188px; }
  .headline--flight { top: 590px; font-size: 236px; letter-spacing: -4px; }
  .headline--lessons { top: 820px; font-size: 140px; }
  .note {
    position: absolute; left: 0; width: 100%; text-align: center;
    font-family: "Bebas Neue", sans-serif; color: var(--white); line-height: 1;
  }
  .note--small { font-size: 64px; }
  .note--offer { top: 982px; }
  .note--age { top: 1032px; font-size: 128px; }
  .note--training { top: 1248px; }
  .note--included { top: 1530px; }
  .divider { position: absolute; left: 113px; width: 872px; height: 2px; background: rgba(255,255,255,.35); }
  .divider--one { top: 1210px; }
  .divider--two { top: 1503px; }
  .solo-pill {
    position: absolute; left: 169px; top: 1328px; width: 759px; height: 128px;
    border-radius: 64px; background: var(--white); color: var(--navy);
    font-family: "Bebas Neue", sans-serif; font-size: 116px; line-height: 134px; text-align: center;
  }
  .price { position: absolute; left: 404px; top: 1616px; width: 306px; height: 306px; }
  .price__label {
    position: absolute; inset: 0; display: flex; align-items: center; justify-content: center;
    font-family: "Bebas Neue", sans-serif; font-size: 118px; color: var(--white);
  }
  .photo {
    position: absolute; border-radius: 50%;
    border: 12px solid var(--ring); box-shadow: 0 0 0 10px var(--white);
  }
  .photo--field { left: 99px; top: 1717px; width: 338px; height: 338px;
    background: linear-gradient(180deg, #8fb0d8 0%, #c9d6df 35%, #5d8a2f 60%, #3f6d22 100%); }
  .photo--glider { left: 692px; top: 1712px; width: 338px; height: 338px;
    background: linear-gradient(180deg, #2f6fc4 0%, #9bbde6 45%, #6a9a36 65%, #487a24 100%); }
  .photo--sky { left: 377px; top: 1977px; width: 360px; height: 360px;
    background: radial-gradient(circle at 40% 40%, #a8c3ea 0%, #5c86cf 55%, #2f58b0 100%); }
  .url {
    position: absolute; left: 0; top: 2350px; width: 100%; text-align: center;
    font-family: "Roboto Condensed", sans-serif; font-weight: 700; font-size: 104px;
    color: var(--navy); letter-spacing: -1px;
  }
</style>
</head>
<body>
  <main class="rollup">
    <svg class="rollup__backdrop" width="1100" height="2588" viewBox="0 0 1100 2588">
      <defs>
        <linearGradient id="hangar" x1="0" y1="0" x2="0" y2="1">
          <stop offset="0" stop-color="#d9d9d9"/>
          <stop offset="0.6" stop-color="#bdbdbd"/>
          <stop offset="1" stop-color="#f4f4f4"/>
        </linearGradient>
      </defs>
      <rect width="1100" height="2588" fill="#f2f2f2"/>
      <rect x="0" y="1890" width="1100" height="500" fill="url(#hangar)" role="img" aria-label="Faded black and white photo of gliders parked on the airfield"/>
      <polygon points="0,0 1100,0 1100,1788 550,2400 0,1788" fill="#1a2055"/>
      <polygon points="0,0 1100,0 550,300" fill="#ffffff"/>
    </svg>

    <div class="club-mark">
      <span class="club-mark__dot"></span>
      <span class="club-mark__name">Luftsportgruppe<br>Tarnholm e.V.</span>
    </div>

    <h1>
      <span class="headline headline--free">FREE</span>
      <span class="headline headline--flight">FLIGHT</span>
      <span class="headline headline--lessons">LESSONS</span>
    </h1>

    <p class="note note--small note--offer">Offer only applies to people up &nbsp;to the</p>
    <p class="note note--age">Age of 25</p>
    <div class="divider divider--one"></div>
    <p class="note note--small note--training">Is training on the glider up to the</p>
    <div class="solo-pill">First solo flight</div>
    <div class="divider divider--two"></div>
    <p class="note note--small note--included">Included in the flat rate of</p>

    <div class="photo photo--field" role="img" aria-label="Photo of gliders and members on the grass airfield"></div>
    <div class="photo photo--glider" role="img" aria-label="Photo of a white glider tail on the grass under a blue sky"></div>
    <div class="photo photo--sky" role="img" aria-label="Photo of a white glider flying in a blue sky"></div>

    <div class="price">
      <svg width="306" height="306" viewBox="-153 -153 306 306">
        <polygon fill="#e8141c" points="0,-153 14,-130 35,-149 43,-124 68,-137 69,-111 96,-119 91,-93 119,-96 108,-72 135,-71 119,-49 145,-44 125,-26 150,-16 128,-4 151,12 126,20 144,38 119,42 133,64 107,63 116,87 91,81 95,107 71,95 70,122 48,106 43,132 24,113 15,139 0,118 -15,139 -24,113 -43,132 -48,106 -70,122 -71,95 -95,107 -91,81 -116,87 -107,63 -133,64 -119,42 -144,38 -126,20 -151,12 -128,-4 -150,-16 -125,-26 -145,-44 -119,-49 -135,-71 -108,-72 -119,-96 -91,-93 -96,-119 -69,-111 -68,-137 -43,-124 -35,-149 -14,-130"/>
      </svg>
      <span class="price__label">€300</span>
    </div>

    <p class="url">www.lgk-tarnholm.de</p>
  </main>
</body>
</html>
```